KLO Kelp Lumen Oasis company brochure

We need the design of brochure of a company that provides consultancy, design and supply of key equipment in the field of Wastewater, clean water, organic waste anaerobic treatment and green energy production for Industries. The attached files are:
KLO wording in english that describes activities
Some drawings (useful for design)
Presentation (in italian)
It would be nice to have a 4 pages brochure possibly in double language (english and italian).

Target Market(s)

water and waste

Industry/Entity Type

It Company

Colors

Designer to choose colors to be used in the design.

Requirements
Must have
• use the logo KLO as per attached docs

```html
<!DOCTYPE html>
<html lang="it">
<head>
<meta charset="utf-8">
<title>KLO Kelp Lumen Oasis – Brochure</title>
<link href="https://fonts.googleapis.com/css2?family=Oswald:wght@400;500;600&family=Lato:wght@400;700&display=swap" rel="stylesheet">
<style>
  :root{
    --bg:#d6d6d6;
    --orange:#f05a14;
    --crimson:#c8102e;
    --blue:#0d5c9c;
    --green:#3aa02c;
    --ink:#2a2a2a;
    --white:#ffffff;
  }
  *{margin:0;padding:0;box-sizing:border-box}
  html,body{width:1200px;height:1200px;overflow:hidden;background:var(--bg)}
  body{position:relative;font-family:"Lato",sans-serif;color:var(--ink)}
  .spread{position:absolute;left:194px;width:817px;height:582px;background:var(--white);overflow:hidden;box-shadow:0 3px 8px rgba(0,0,0,.25)}
  .spread--cover{top:8px}
  .spread--inside{top:610px}
  .page{position:absolute;top:0;width:409px;height:100%}
  .page--left{left:0}
  .page--right{left:408px;width:409px}
  .photo{position:absolute}
  .cover-back-photo{inset:0;background:linear-gradient(180deg,#9a9a9a 0%,#cfcfcf 42%,#8d8d8d 60%,#4a4a4a 85%,#333 100%)}
  .cover-front-photo{inset:0;background:linear-gradient(180deg,#9d8ed0 0%,#d8a7c0 22%,#f2c27c 38%,#f7b23c 45%,#3f4a52 52%,#8a7f84 66%,#5b5a60 82%,#3a3a3c 100%)}
  .bubble{position:absolute;border-radius:50%;border:3px solid var(--white)}
  .bubble--a{left:116px;top:38px;width:136px;height:136px;background:linear-gradient(160deg,#6f9a4a,#b9a88a 55%,#6e8f45)}
  .bubble--b{left:250px;top:16px;width:100px;height:100px;background:linear-gradient(180deg,#e8eef2,#50565a 60%,#6b7f54)}
  .bubble--c{left:226px;top:134px;width:100px;height:100px;background:linear-gradient(180deg,#c8d0d8,#a8adb2 60%,#e4e6e8)}
  .brand-disc{position:absolute;left:67px;top:394px;width:92px;height:92px;border-radius:50%;background:var(--white);display:flex;align-items:center;justify-content:center;text-align:center}
  .brand-disc span{font-family:"Lato",sans-serif;font-weight:700;font-size:13px;line-height:1.15;color:var(--blue)}
  .contacts{position:absolute;left:66px;top:500px;color:var(--white);font-family:"Oswald",sans-serif;list-style:none}
  .contacts li{display:flex;align-items:center;gap:9px;line-height:1.1;margin-bottom:3px}
  .contacts svg{width:8px;height:8px;flex:none}
  .contacts .big{font-size:11px;font-weight:500}
  .contacts .small{font-size:7px}
  .contacts .pad{padding-left:17px}
  .name-box{position:absolute;right:0;top:16px;width:236px;height:71px;background:var(--white);display:flex;align-items:center;justify-content:center;gap:10px}
  .name-box i{width:14px;height:14px;background:var(--green);display:block}
  .name-box span{font-family:"Lato",sans-serif;font-weight:700;font-size:17px;color:var(--blue)}
  .cover-title{position:absolute;right:56px;top:492px;text-align:right;color:var(--white)}
  .cover-title h1{font-family:"Oswald",sans-serif;font-weight:600;font-size:26px;color:var(--orange);letter-spacing:-.2px;line-height:1.1}
  .cover-title p{font-family:"Oswald",sans-serif;font-weight:400;font-size:12px;line-height:1.3;margin-top:4px}
  .band{position:absolute;top:0;left:0;width:100%;height:192px}
  .band--blue{background:linear-gradient(160deg,#1a4f78,#2f7fb3 50%,#1d6aa0)}
  .band--orange{background:linear-gradient(180deg,#f3a88a 0%,#ee6a2a 30%,#e55a12 70%,#d9500e)}
  .band-title{position:absolute;font-family:"Oswald",sans-serif;font-weight:500;font-size:19px;color:var(--white);text-shadow:0 1px 3px rgba(0,0,0,.5)}
  .band-title--left{left:65px;top:166px}
  .band-title--right{left:66px;top:160px}
  .bullets{position:absolute;left:65px;list-style:none;font-size:8px;line-height:1.3}
  .bullets li{position:relative;padding-left:18px;margin-bottom:3.5px}
  .bullets li::before{content:"";position:absolute;left:0;top:3px;width:3px;height:3px;border-radius:50%;background:var(--green)}
  .bullets--supply{top:213px;width:300px}
  .bullets--why{top:420px;width:300px}
  .why-title{position:absolute;left:65px;top:346px;font-family:"Oswald",sans-serif;font-weight:500;font-size:18px;color:var(--blue)}
  .why-intro{position:absolute;left:65px;top:377px;width:280px;font-size:8px;line-height:1.3}
  .tech{position:absolute;left:66px;top:210px;width:300px;list-style:none}
  .tech > li{margin-bottom:10px}
  .tech h3{font-family:"Lato",sans-serif;font-weight:700;font-size:11px;color:var(--crimson);display:flex;gap:10px}
  .tech h3 b{color:var(--ink);width:8px}
  .tech ol{list-style:none;margin:6px 0 0 18px;font-size:8px;line-height:1.3}
  .tech ol li{display:flex;gap:10px;margin-bottom:2px}
  .tech ol li em{font-style:normal;width:8px;flex:none}
  .plant-drawing{position:absolute;left:0;bottom:0;width:100%;height:130px;background:linear-gradient(180deg,rgba(255,255,255,0),#ececec 60%,#e0e0e0)}
</style>
</head>
<body>

<section class="spread spread--cover">
  <div class="page page--left">
    <div class="photo cover-back-photo" role="img" aria-label="Black and white photo of a wastewater treatment basin with steel bridge"></div>
    <div class="bubble bubble--a" role="img" aria-label="Photo of an outdoor treatment plant in a field"></div>
    <div class="bubble bubble--b" role="img" aria-label="Photo of an anaerobic digester tank"></div>
    <div class="bubble bubble--c" role="img" aria-label="Photo of stainless steel silos"></div>
    <div class="brand-disc"><span>KLO<br>Kelp Lumen<br>Oasis</span></div>
    <ul class="contacts">
      <li class="big"><svg viewBox="0 0 10 10"><path fill="#fff" d="M2 1l2 2-1 1c.6 1.3 1.7 2.4 3 3l1-1 2 2-1.5 1.5C4 9 1 6 .5 2.5z"/></svg>011.5550192</li>
      <li class="big"><svg viewBox="0 0 10 10"><rect x="2.5" y=".5" width="5" height="9" rx="1" fill="none" stroke="#fff"/></svg>335 555 0148</li>
      <li class="small"><svg viewBox="0 0 10 10"><rect x="1" y="2.5" width="8" height="5" fill="#fff"/></svg>INFO@KLO-OASIS.EXAMPLE</li>
      <li class="small"><svg viewBox="0 0 10 10"><path fill="#fff" d="M5 0a3.5 3.5 0 0 0-3.5 3.5C1.5 6 5 10 5 10s3.5-4 3.5-6.5A3.5 3.5 0 0 0 5 0z"/></svg>KLO SRL - VIA DELLE ALGHE 12 - ITALY</li>
      <li class="small pad">PIVA: 00000000000</li>
    </ul>
  </div>
  <div class="page page--right">
    <div class="photo cover-front-photo" role="img" aria-label="Photo of treatment basins at sunset"></div>
    <div class="name-box"><i></i><span>KLO Kelp Lumen Oasis</span></div>
    <div class="cover-title">
      <h1>SOLUZIONI COMPLETE PER</h1>
      <p>la depurazione, riuso dell’acqua, recupero prodotti e<br>minimizzazione delle emissioni</p>
    </div>
  </div>
</section>

<section class="spread spread--inside">
  <div class="page page--left">
    <div class="band band--blue" role="img" aria-label="Blue toned photo of a clarifier scraper mechanism"></div>
    <h2 class="band-title band-title--left">KLO FORNISCE:</h2>
    <ul class="bullets bullets--supply">
      <li>Studi di fattibilità</li>
      <li>Prove pilota con i propri laboratori interni</li>
      <li>Progettazione di processo (oltre 240 referenze)<br>Basic and detailed engineering</li>
      <li>Ingegneria di base e di dettaglio</li>
      <li>Supervisione alla costruzione e all’avvio</li>
      <li>Competenza nella gestione degli impianti con oltre 20 anni di gestione di processi biologici e chimico/fisici</li>
    </ul>
    <h2 class="why-title">PERCHE SCEGLIERE KLO?</h2>
    <p class="why-intro">KLO ha l’obiettivo innanzitutto di risolvere ogni problema ambientale del cliente con la migliore soluzione sia in termini di risparmio di investimento che di costi di esercizio.</p>
    <ul class="bullets bullets--why">
      <li>KLO innanzitutto identifica le inefficienze nei processi produttivi e le elimina</li>
      <li>Solo quando la riduzione delle emissioni alla fonte non è più ragionevolmente attuabile allora KLO propone il sistema di trattamento più affidabile al cliente</li>
      <li>KLO ha competenze approfondite su svariati processi biologici e chimici</li>
    </ul>
  </div>
  <div class="page page--right">
    <div class="band band--orange" role="img" aria-label="Orange toned photo of a large digester tank with walkways"></div>
    <h2 class="band-title band-title--right">TECNOLOGIA PROPOSTE:</h2>
    <ol class="tech">
      <li>
        <h3><b>1.</b>Processi biologici</h3>
        <ol>
          <li><em>a.</em>Ossidazione, nitro/denitro, rimozione-P</li>
          <li><em>b.</em>Recupero Azoto e produzione di fertilizzanti a lento rilascio</li>
          <li><em>c.</em>Processi anaerobici: UASB, frazione organica rifiuti, rimozione odori</li>
          <li><em>d.</em>Recupero metalli</li>
        </ol>
      </li>
      <li><h3><b>2.</b>Recupero prodotti ad alto valore aggiunto</h3></li>
      <li>
        <h3><b>3.</b>Processi chimico/fisici</h3>
        <ol>
          <li><em>a.</em>Flottazione ad aria disciolta</li>
          <li><em>b.</em>Filtrazione a membrane</li>
          <li><em>c.</em>Ossidazioni chimiche</li>
          <li><em>d.</em>Disinfezione</li>
        </ol>
      </li>
      <li><h3><b>4.</b>Recupero e riuso dell’acqua</h3></li>
    </ol>
  </div>
  <div class="plant-drawing" role="img" aria-label="Line drawing of a treatment plant with tanks and buildings"></div>
</section>

</body>
</html>
```